ULMIRA card Technical Architecture

Hello everyone ULMIRA: It is a consulting firm in Architecture and Construction. I require a card duplexing, sober, elegant, classic but not boring. Update 1: Use the following data for the card. Name: Gonzalo Pereda Mauricio Villalta Position: COO Twitter: @ulmiraAT Homepage: ulmira-example.com home address not include the participation of all thank you.

Target Market(s)

Construction companies, Architects and Consulting Engineers

Industry/Entity Type

Consulting

Contact Information for Business Card

Los campos que debe tener:
Nombre, Cargo, email, homepage y twitter

Font styles to use
Serif
Sans Serif
Other font styles liked:
• Me gustan playfair display, open sans y roboto, pero estoy sujeto a sus propuestas

Requirements
Must have
• Colors: Present combined proposals in white, red, gray and black Update 1: The two names must be clearly differentiated from the two surnames
Nice to have
• They are free to present their best proposals. I will bring them immediate feedback to the extent you can go see their designs. Complete data for card and logo files will give the winner the

```html
<!DOCTYPE html>
<html lang="en">
<head>
<meta charset="utf-8">
<title>ULMIRA business card</title>
<link rel="stylesheet" href="https://fonts.googleapis.com/css2?family=Josefin+Sans:wght@300;400&family=Open+Sans:wght@400;600&display=swap">
<style>
  :root {
    --red: #b0051a;
    --red-dark: #7a0010;
    --red-deep: #5e000c;
    --white: #ffffff;
    --black: #1a1a1a;
    --stage: #e9e7e5;
    --rule: #c9a0a5;
  }
  * { margin: 0; padding: 0; box-sizing: border-box; }
  html, body { width: 1200px; height: 900px; overflow: hidden; }
  body { background: var(--stage); position: relative; font-family: "Open Sans", sans-serif; }

  .card { position: absolute; background: var(--white); overflow: hidden; box-shadow: 0 6px 18px rgba(0,0,0,.18); }

  /* Front card */
  .card--front { left: 78px; top: 34px; width: 588px; height: 364px; }
  .card--front .brand { position: absolute; left: 34px; top: 48px; }
  .brand-name {
    font-family: "Josefin Sans", sans-serif; font-weight: 300;
    color: var(--black); letter-spacing: 0.22em; line-height: 1;
  }
  .brand-tagline {
    font-family: "Josefin Sans", sans-serif; font-weight: 400;
    color: var(--red); letter-spacing: 0.22em; line-height: 1;
  }
  .card--front .brand-name { font-size: 44px; }
  .card--front .brand-tagline { font-size: 15px; margin-top: 14px; }

  .info-band {
    position: absolute; left: 0; top: 153px; width: 100%; height: 211px;
    background: linear-gradient(180deg, var(--red) 0%, var(--red-dark) 100%);
    color: var(--white); padding: 16px 0 0 31px;
  }
  .person-name { font-weight: 600; font-size: 20px; line-height: 1.2; }
  .person-role { font-size: 15px; line-height: 1.3; }
  .contact-list { list-style: none; margin-top: 26px; }
  .contact-list li { display: flex; align-items: center; font-size: 15px; height: 24.5px; }
  .contact-list svg { width: 12px; height: 12px; margin-right: 9px; fill: var(--white); }

  /* Back card */
  .card--back { left: 388px; top: 505px; width: 567px; height: 352px; }
  .back-band {
    position: absolute; left: 0; width: 100%; height: 75px;
    background: radial-gradient(ellipse at 50% 50%, var(--red) 0%, var(--red-dark) 70%, var(--red-deep) 100%);
  }
  .back-band--top { top: 0; }
  .back-band--bottom { bottom: 0; height: 74px; }
  .card--back .brand {
    position: absolute; left: 0; right: 0; top: 196px; text-align: center;
  }
  .brand-lockup { display: inline-flex; align-items: center; gap: 14px; }
  .brand-mark { width: 22px; height: 22px; background: var(--red); }
  .card--back .brand-name { font-size: 44px; }
  .card--back .brand-tagline { font-size: 15px; margin-top: 12px; }
</style>
</head>
<body>

  <section class="card card--front" aria-label="Card front">
    <div class="brand">
      <div class="brand-name">ULMIRA</div>
      <div class="brand-tagline">ARQUITECTURA TÉCNICA</div>
    </div>
    <div class="info-band">
      <div class="person-name">Tomas Rivera</div>
      <div class="person-role">Managing Director</div>
      <ul class="contact-list">
        <li>
          <svg viewBox="0 0 12 12" aria-hidden="true"><path d="M2.5 0.5 L4.5 0.5 L5.2 3 L3.8 4.2 C4.5 5.8 6.2 7.5 7.8 8.2 L9 6.8 L11.5 7.5 L11.5 9.5 C11.5 10.8 10.5 11.5 9.5 11.5 C4.5 11 1 7.5 0.5 2.5 C0.5 1.3 1.3 0.5 2.5 0.5 Z"/></svg>
          (000)-555-0142
        </li>
        <li>
          <svg viewBox="0 0 12 12" aria-hidden="true"><path d="M0.5 2 H11.5 V10 H0.5 Z M1.5 3 V3.4 L6 6.5 L10.5 3.4 V3 Z"/></svg>
          info@ulmira-example.com
        </li>
        <li>
          <svg viewBox="0 0 12 12" aria-hidden="true"><circle cx="6" cy="6" r="5.5"/><path d="M0.5 6 H11.5 M6 0.5 C3.5 3 3.5 9 6 11.5 M6 0.5 C8.5 3 8.5 9 6 11.5" stroke="#a3041a" stroke-width="0.9" fill="none"/></svg>
          www.ulmira-example.com
        </li>
        <li>
          <svg viewBox="0 0 12 12" aria-hidden="true"><circle cx="6" cy="6" r="5.5"/></svg>
          @ulmiraAT
        </li>
      </ul>
    </div>
  </section>

  <section class="card card--back" aria-label="Card back">
    <div class="back-band back-band--top"></div>
    <div class="brand">
      <div class="brand-lockup">
        <span class="brand-mark" aria-hidden="true"></span>
        <span class="brand-name">ULMIRA</span>
      </div>
      <div class="brand-tagline">ARQUITECTURA TÉCNICA</div>
    </div>
    <div class="back-band back-band--bottom"></div>
  </section>

</body>
</html>
```